Job Recruiting Agemcy

almost like my current site www.plorvex.com but with these changes see and what i meant about the across the to the site says home job companies categories pages blog and login sign up that should only be the 4 i said only 1 home 2 industries 3 jobs 4 contact us. and remove latest blog post and our partners because that's not us we have to post acuarte information thanks and the name of the company if your using is is work and careful hiring partners and want it easy for us to post and remove jobs and where it emails us every resume or person that applies

Requirements
Must have
• must send email to us when an application is submitted and try to incorparate the colors of current site
Nice to have
• i want a pretty basic site for now just like the one i have but with all thats above were its easy for me being the own to be able to post jobs and everything

```html
<!DOCTYPE html>
<html lang="en">
<head>
<meta charset="utf-8">
<title>Plorvex — Work and Careful Hiring Partners</title>
<link rel="stylesheet" href="https://fonts.googleapis.com/css2?family=Rajdhani:wght@500;600;700&family=Roboto:ital,wght@0,400;1,400&display=swap">
<style>
:root{
  --green:#2f6847;
  --green-dark:#28593d;
  --red:#d6434f;
  --purple:#6a1fd0;
  --blush:#f4f0f0;
  --ink:#2b2b2b;
  --muted:#5c5c5c;
  --white:#ffffff;
}
*{margin:0;padding:0;box-sizing:border-box}
html,body{width:1200px;height:3039px;overflow:hidden}
body{position:relative;background:var(--white);font-family:'Roboto',sans-serif;color:var(--ink)}
.abs{position:absolute}
.head{font-family:'Rajdhani',sans-serif}

/* header */
.site-header{left:0;top:0;width:1200px;height:100px;background:var(--green)}
.brand{left:130px;top:28px;display:flex;align-items:center;gap:10px;font-family:'Rajdhani',sans-serif;font-weight:700;font-size:26px;color:var(--white);letter-spacing:1px}
.brand-dot{width:16px;height:16px;border-radius:50%;background:var(--red)}
.main-nav{right:112px;top:38px;display:flex;gap:33px;font-family:'Rajdhani',sans-serif;font-weight:600;font-size:14px;color:var(--white);letter-spacing:.5px}
.main-nav .active{border-bottom:1px solid var(--white);padding-bottom:3px}
.main-nav svg{vertical-align:-1px;margin-right:4px}

/* hero */
.hero-photo{left:0;top:100px;width:1200px;height:650px;background:linear-gradient(100deg,#3c3c44 0%,#5c5650 35%,#8a7c6a 60%,#c4a07a 78%,#e8e6e4 100%)}
.hero-shade{left:0;top:100px;width:1200px;height:650px;background:linear-gradient(90deg,rgba(0,0,0,.45),rgba(0,0,0,0) 60%)}
.hero-kicker{left:59px;top:300px;font-family:'Rajdhani',sans-serif;font-weight:500;font-size:21px;color:var(--white)}
.hero-title{left:59px;top:337px;font-family:'Rajdhani',sans-serif;font-weight:700;font-size:40px;color:var(--white);letter-spacing:.5px}
.field{top:407px;width:250px;height:52px;border:1px solid rgba(255,255,255,.85);border-radius:26px;color:rgba(255,255,255,.9);font-family:'Rajdhani',sans-serif;font-weight:500;font-size:18px;padding:0 22px;display:flex;align-items:center;justify-content:space-between}
.btn{display:flex;align-items:center;justify-content:center;border-radius:26px;font-family:'Rajdhani',sans-serif;font-weight:600;color:var(--white);letter-spacing:.5px}
.btn-green{background:var(--green)}
.btn-red{background:var(--red)}
.hero-search{left:56px;top:484px;width:180px;height:50px;font-size:19px}
.ring-arrow{border:1px solid currentColor;border-radius:50%;display:flex;align-items:center;justify-content:center}
.hero-arrow{top:556px;width:32px;height:32px;color:var(--white)}

/* about */
.about-bg{left:0;top:740px;width:1200px;height:655px;background:linear-gradient(90deg,#fdf6f7,#ffffff 50%,#fdf6f8)}
.about-photo{left:87px;top:813px;width:500px;height:500px;border-radius:50%;background:linear-gradient(140deg,#b89a8c,#7a6e6a 45%,#4a4644);border-right:4px solid var(--red)}
.section-title{font-family:'Rajdhani',sans-serif;font-weight:700;color:var(--red);letter-spacing:1px}
.about-title{left:625px;top:875px;font-size:46px}
.about-bar{left:625px;top:948px;width:120px;height:5px;background:var(--purple)}
.about-text{left:625px;top:980px;width:455px;font-size:15.5px;line-height:34.5px;color:var(--muted);text-align:justify}
.about-btn{left:625px;top:1133px;width:155px;height:50px;font-size:17px}

/* industries */
.industries{left:0;top:1395px;width:1200px;height:558px;background:var(--blush)}
.ind-title{left:0;top:1460px;width:1200px;text-align:center;font-size:42px}
.ind-card{top:1539px;width:317px;height:274px;box-shadow:0 1px 4px rgba(0,0,0,.2)}
.ind-caption{width:317px;top:1831px;text-align:center;font-family:'Rajdhani',sans-serif;font-weight:600;font-size:13.5px;line-height:28px;color:var(--ink);letter-spacing:.3px}
.ind-arrow{top:1649px;width:51px;height:51px;color:#222}

/* testimonials */
.testi-bg{left:0;top:1953px;width:1200px;height:590px;background:#fbfbfb}
.testi-photo{left:111px;top:2053px;width:355px;height:385px;background:linear-gradient(120deg,#e8ecef,#c9c2bb 55%,#8e7c6e);box-shadow:0 1px 4px rgba(0,0,0,.2)}
.testi-title{left:489px;top:2128px;font-size:42px}
.testi-quote{left:495px;top:2187px;width:520px;font-style:italic;font-size:15px;line-height:30px;color:var(--muted)}
.testi-name{left:496px;top:2259px;font-size:15px;color:var(--red)}
.testi-arrow{top:2302px;width:32px;height:32px;color:#333}
.quote-mark{left:970px;top:2260px;font-family:'Rajdhani',sans-serif;font-weight:700;font-size:170px;line-height:1;color:rgba(214,67,79,.35)}

/* cta */
.cta{left:0;top:2543px;width:1200px;height:310px;background:var(--blush)}
.cta-kicker{left:0;top:2600px;width:1200px;text-align:center;font-family:'Rajdhani',sans-serif;font-weight:600;font-size:26px;letter-spacing:1.5px}
.cta-line{left:0;top:2642px;width:1200px;text-align:center;font-family:'Rajdhani',sans-serif;font-weight:500;font-size:27px;letter-spacing:1.5px}
.cta-rule{left:458px;top:2696px;width:285px;height:3px;background:var(--red)}
.cta-btn{top:2743px;width:154px;height:51px;font-size:17px}

/* footer */
.site-footer{left:0;top:2853px;width:1200px;height:186px;background:var(--green)}
.foot-nav{left:0;top:2893px;width:1200px;display:flex;justify-content:center;gap:50px;font-family:'Rajdhani',sans-serif;font-weight:500;font-size:18px;color:var(--white);letter-spacing:.5px}
.social{left:0;top:2948px;width:1200px;display:flex;justify-content:center;gap:18px}
.social span{width:19px;height:19px;border-radius:3px;background:var(--white)}
.copy{left:0;top:2992px;width:1200px;text-align:center;font-size:15px;color:var(--white)}
</style>
</head>
<body>

<header class="abs site-header">
  <div class="abs brand"><span class="brand-dot"></span>PLORVEX</div>
  <nav class="abs main-nav">
    <span class="active">HOME</span>
    <span>INDUSTRIES</span>
    <span>JOBS</span>
    <span>CONTACT US</span>
    <span><svg width="11" height="12" viewBox="0 0 11 12"><circle cx="5.5" cy="3.2" r="3" fill="#fff"/><path d="M0 12c0-4 2.5-5.5 5.5-5.5S11 8 11 12z" fill="#fff"/></svg>LOGIN</span>
    <span><svg width="12" height="12" viewBox="0 0 24 24"><path d="M6.6 10.8a15.1 15.1 0 0 0 6.6 6.6l2.2-2.2a1 1 0 0 1 1-.25 11.4 11.4 0 0 0 3.6.57 1 1 0 0 1 1 1V20a1 1 0 0 1-1 1A17 17 0 0 1 3 4a1 1 0 0 1 1-1h3.5a1 1 0 0 1 1 1c0 1.25.2 2.45.57 3.57a1 1 0 0 1-.25 1z" fill="#fff"/></svg>CALL NOW- 555-010-2040</span>
  </nav>
</header>

<section>
  <div class="abs hero-photo" role="img" aria-label="Job candidates seated in a waiting room reviewing their resumes"></div>
  <div class="abs hero-shade"></div>
  <p class="abs hero-kicker">Search from 0 job offers</p>
  <h1 class="abs hero-title">YOUR CAREER STARTS HERE!</h1>
  <div class="abs field" style="left:56px">Keywords
    <svg width="16" height="16" viewBox="0 0 16 16"><circle cx="6.5" cy="6.5" r="4.8" stroke="#fff" stroke-width="2" fill="none"/><path d="M10 10l4.5 4.5" stroke="#fff" stroke-width="2.4" stroke-linecap="round"/></svg></div>
  <div class="abs field" style="left:316px">Locations
    <svg width="12" height="16" viewBox="0 0 12 16"><path d="M6 0a6 6 0 0 1 6 6c0 4.5-6 10-6 10S0 10.5 0 6a6 6 0 0 1 6-6z" fill="#fff"/><circle cx="6" cy="6" r="2.2" fill="#555"/></svg></div>
  <div class="abs btn btn-green hero-search">SEARCH</div>
  <div class="abs ring-arrow hero-arrow" style="left:1011px"><svg width="10" height="14" viewBox="0 0 10 14"><path d="M8 1L2 7l6 6" stroke="#fff" stroke-width="1.6" fill="none"/></svg></div>
  <div class="abs ring-arrow hero-arrow" style="left:1054px"><svg width="10" height="14" viewBox="0 0 10 14"><path d="M2 1l6 6-6 6" stroke="#fff" stroke-width="1.6" fill="none"/></svg></div>
  <svg class="abs" style="left:0;top:600px" width="1200" height="160" viewBox="0 0 1200 160" aria-hidden="true">
    <path d="M0 160V90 C200 110 330 90 520 50 C760 5 980 0 1200 80 V160Z" fill="var(--green)"/>
    <path d="M0 160V85 C180 105 300 95 500 62 C720 25 980 20 1200 82 V160Z" fill="var(--red)"/>
    <path d="M0 160V130 C220 120 420 80 640 50 C860 25 1050 35 1200 85 V160Z" fill="var(--green)"/>
    <path d="M0 160V88 C160 100 300 95 480 66 C720 28 980 30 1200 84 V160Z" fill="#ffffff" transform="translate(0,24)"/>
    <path d="M0 90 C180 105 320 96 520 60" stroke="none" fill="none"/>
  </svg>
</section>

<section>
  <div class="abs about-bg"></div>
  <div class="abs about-photo" role="img" aria-label="Two colleagues talking on a sofa in a bright office lounge"></div>
  <h2 class="abs section-title about-title">ABOUT US</h2>
  <div class="abs about-bar"></div>
  <p class="abs about-text">We have over 35 years of Specialized Recruiting and souring experience. We cover a broad spectrum of industries to include some of the top aerospace and pharmaceutical commercial companies of today.</p>
  <div class="abs btn btn-green about-btn">READ MORE</div>
</section>

<section>
  <div class="abs industries"></div>
  <h2 class="abs section-title ind-title">INDUSTRIES WE SUPPORT</h2>
  <div class="abs ring-arrow ind-arrow" style="left:48px"><svg width="10" height="16" viewBox="0 0 10 16"><path d="M8 2L2 8l6 6" stroke="#222" stroke-width="2" fill="none"/></svg></div>
  <div class="abs ring-arrow ind-arrow" style="left:1098px"><svg width="10" height="16" viewBox="0 0 10 16"><path d="M2 2l6 6-6 6" stroke="#222" stroke-width="2" fill="none"/></svg></div>
  <div class="abs ind-card" style="left:111px;background:linear-gradient(180deg,#6d9fd6,#9cc2e8 45%,#2d5f8e 60%,#1d4a78)" role="img" aria-label="Passenger jet flying above a coastline"></div>
  <div class="abs ind-card" style="left:441px;background:linear-gradient(110deg,#d8dee0,#eef0f0 45%,#c9a48a 70%,#51606e)" role="img" aria-label="Pharmacist handing medicine to a customer"></div>
  <div class="abs ind-card" style="left:771px;background:linear-gradient(180deg,#7c7f82,#a9abab 40%,#c8c8c6 70%,#9a9b9a)" role="img" aria-label="Freight truck driving on a highway"></div>
  <p class="abs ind-caption" style="left:111px">AERO SPACE- ALTAIR FLIGHT CONTROLS,<br>ORBITLINE VOLTARIS ELECTRIC</p>
  <p class="abs ind-caption" style="left:441px">PHARMACEUTICAL/ BIOTECHNOLOGY GENOVA LIFE SCIENCES ,<br>LUMA COSMETICS</p>
  <p class="abs ind-caption" style="left:771px">TRANSPORTATION- RIDGEWAY TRUCKING, PARCELRUN</p>
</section>

<section>
  <div class="abs testi-bg"></div>
  <div class="abs testi-photo" role="img" aria-label="Smiling woman with glasses holding a tablet at her desk"></div>
  <h2 class="abs section-title testi-title">TESTIMONIALS</h2>
  <p class="abs testi-quote">I just can't get enough of Workfind. I want to get a T-Shirt with Workfind on it so I can show it off to everyone. This is simply unbelievable!</p>
  <p class="abs testi-name">MARCUS DELANEY</p>
  <div class="abs ring-arrow testi-arrow" style="left:492px"><svg width="10" height="14" viewBox="0 0 10 14"><path d="M8 1L2 7l6 6" stroke="#333" stroke-width="1.6" fill="none"/></svg></div>
  <div class="abs ring-arrow testi-arrow" style="left:535px"><svg width="10" height="14" viewBox="0 0 10 14"><path d="M2 1l6 6-6 6" stroke="#333" stroke-width="1.6" fill="none"/></svg></div>
  <div class="abs quote-mark" aria-hidden="true">&ldquo;</div>
</section>

<section>
  <div class="abs cta"></div>
  <h3 class="abs cta-kicker">SEEKING FOR A JOB?</h3>
  <p class="abs cta-line">BROWSE HUNDREDS OF JOB OFFERS AND FIND THE BEST SUITABLE POSITION</p>
  <div class="abs cta-rule"></div>
  <div class="abs btn btn-green cta-btn" style="left:437px">SEARCH JOBS</div>
  <div class="abs btn btn-red cta-btn" style="left:609px">ADD A RESUME</div>
</section>

<footer class="abs site-footer"></footer>
<nav class="abs foot-nav"><span>HOME</span><span>INDUSTRIES</span><span>JOBS</span><span>CONTACT US</span></nav>
<div class="abs social" aria-label="Social links"><span></span><span></span><span></span><span></span></div>
<p class="abs copy">© 2020 All Rights Reserved</p>

</body>
</html>
```